Business Card Design

Tumble Harbor is a Laundromat Store
we provide wash and Fold service to Customers who are busy with their life and can not come to the store and do laundry
we have customers who drop their laundry at the store
but now i want to provide service to customers who are not able to come to the store to drop. i will go to their address and pickup the laundry and get it washed folded and delivered
Updates
Can you use the colour in you design which i uploaded and also fusha fluorescent green bright pink
Target Market(s)
all works of life who don't have time to do laundry
Industry/Entity Type
Store
Contact Information for Business Card
TumbleHarbor Laundromat
247 Mallory Street
Lynn MA 01938
Look and feel
Each slider illustrates characteristics of the customer's brand and the style your logo design should communicate.

```html
<!DOCTYPE html>
<html lang="en">
<head>
<meta charset="utf-8">
<title>TumbleHarbor Laundromat – Business Card</title>
<link href="https://fonts.googleapis.com/css2?family=Lato:wght@400;700;900&display=swap" rel="stylesheet">
<style>
  :root {
    --stage: #3b3b3b;
    --pink: #e91e8c;
    --pink-deep: #c4126f;
    --purple: #8e2a8f;
    --purple-light: #a53ea6;
    --green: #1f9a48;
    --green-deep: #0b6e33;
    --green-light: #5cc36a;
    --teal-edge: #1fb7a6;
    --white: #ffffff;
    --laundry-mixed: #b07a9a;
    --laundry-folded: #7a5a6e;
  }
  * { margin: 0; padding: 0; box-sizing: border-box; }
  html, body {
    width: 1200px; height: 900px; overflow: hidden;
    background: var(--stage);
    font-family: "Lato", Arial, sans-serif;
  }
  .card {
    position: absolute; left: 80px; top: 130px;
    width: 1040px; height: 640px; overflow: hidden;
    background: radial-gradient(ellipse at 50% 35%, var(--pink) 45%, var(--pink-deep) 100%);
    box-shadow: 0 18px 40px rgba(0,0,0,.45);
  }
  .brand {
    position: absolute; top: 46px; left: 0; width: 100%;
    display: flex; justify-content: center; align-items: center; gap: 14px;
  }
  .brand-mark { width: 34px; height: 34px; background: var(--purple); }
  .brand-name { color: var(--white); font-weight: 700; font-size: 42px; letter-spacing: .5px; }
  .address {
    position: absolute; top: 108px; left: 0; width: 100%; text-align: center;
    color: var(--white); font-size: 23px; letter-spacing: 4px; text-transform: uppercase;
  }
  .phone {
    position: absolute; top: 148px; left: 0; width: 100%; text-align: center;
    color: var(--white); font-size: 27px; font-weight: 700;
  }
  .laundry { position: absolute; border-radius: 18px; }
  .laundry--mixed {
    left: 270px; top: 215px; width: 215px; height: 170px;
    background: radial-gradient(ellipse at 50% 55%, #d8b6c8 0%, var(--laundry-mixed) 70%, rgba(176,122,154,0) 100%);
  }
  .laundry--folded {
    left: 625px; top: 205px; width: 185px; height: 185px;
    background: linear-gradient(180deg, #c8a6b8 0%, #9a4a5a 35%, #556470 65%, var(--laundry-folded) 100%);
  }
  .transform-badge {
    position: absolute; left: 488px; top: 222px; width: 134px; height: 134px;
    border-radius: 50%; background: var(--purple-light);
    color: var(--white); font-weight: 900;
  }
  .transform-badge .from {
    position: absolute; display: block; left: 0; top: 24px; width: 100%;
    text-align: center; font-size: 28px; line-height: 1;
  }
  .transform-badge .to {
    position: absolute; display: block; left: 0; top: 84px; width: 100%;
    text-align: center; font-size: 24px; line-height: 1;
  }
  .transform-badge svg { position: absolute; left: 22px; top: 58px; }
  .band { position: absolute; left: 0; top: 0; }
  .step {
    position: absolute; top: 432px; width: 260px; margin-left: -130px;
    text-align: center; color: var(--white);
  }
  .step-icon {
    width: 112px; height: 112px; margin: 0 auto;
    border-radius: 50%; background: var(--white);
    display: flex; align-items: center; justify-content: center;
    box-shadow: 0 4px 10px rgba(0,0,0,.3);
  }
  .step-icon span { width: 84px; height: 84px; border-radius: 50%; display: block; }
  .step-label { margin-top: 16px; font-size: 20px; font-weight: 700; line-height: 1.25; white-space: nowrap; }
  .arrow { position: absolute; top: 460px; }
</style>
</head>
<body>
<div class="card">
  <svg class="band" width="1040" height="640" viewBox="0 0 1040 640">
    <defs>
      <radialGradient id="bandFill" cx="50%" cy="20%" r="80%">
        <stop offset="0" stop-color="#5cc36a"/>
        <stop offset=".5" stop-color="#1f9a48"/>
        <stop offset="1" stop-color="#0b6e33"/>
      </radialGradient>
    </defs>
    <path d="M0 420 Q520 300 1040 420 L1040 640 L0 640 Z" fill="#1fb7a6"/>
    <path d="M0 428 Q520 310 1040 428 L1040 640 L0 640 Z" fill="url(#bandFill)"/>
  </svg>

  <div class="brand">
    <span class="brand-mark"></span>
    <span class="brand-name">TumbleHarbor Laundromat</span>
  </div>
  <p class="address">247 Mallory Street Lynn MA 01938</p>
  <p class="phone">CALL US: 079 555 01234</p>

  <div class="laundry laundry--mixed" role="img" aria-label="Photo of a pile of dirty mixed laundry"></div>
  <div class="laundry laundry--folded" role="img" aria-label="Photo of a neat stack of folded clean clothes"></div>
  <div class="transform-badge">
    <span class="from">FROM</span>
    <svg width="90" height="20" viewBox="0 0 90 20">
      <path d="M20 5 H86 M80 1 L86 5 L80 9" stroke="#fff" stroke-width="1.6" fill="none"/>
      <path d="M70 15 H4 M10 11 L4 15 L10 19" stroke="#fff" stroke-width="1.6" fill="none"/>
    </svg>
    <span class="to">TO</span>
  </div>

  <div class="step" style="left:180px">
    <div class="step-icon"><span role="img" aria-label="Schedule calendar icon" style="background:radial-gradient(#f2f2f2,#9a9a9a)"></span></div>
    <p class="step-label">You Schedule<br>A Pick-Up</p>
  </div>
  <div class="step" style="left:420px">
    <div class="step-icon"><span role="img" aria-label="House icon" style="background:radial-gradient(#f6c27a,#3f8fd6)"></span></div>
    <p class="step-label">We Pick-Up<br>Your Dirty Laundry</p>
  </div>
  <div class="step" style="left:660px">
    <div class="step-icon"><span role="img" aria-label="Laundry basket and washing icon" style="background:radial-gradient(#c9d66a,#5c6b8a)"></span></div>
    <p class="step-label">We Wash, Dry, Fold<br>&amp; Return Clean Laundry</p>
  </div>
  <div class="step" style="left:890px">
    <div class="step-icon"><span role="img" aria-label="Happy customer emoji icon" style="background:radial-gradient(#ffe45a,#f2b21a)"></span></div>
    <p class="step-label">Enjoy Effortless<br>Clean Laundry</p>
  </div>

  <svg class="arrow" style="left:255px" width="100" height="50" viewBox="0 0 100 50">
    <path d="M6 40 Q50 10 92 28 M82 20 L92 28 L80 34" stroke="#fff" stroke-width="2.5" fill="none"/>
  </svg>
  <svg class="arrow" style="left:495px" width="100" height="50" viewBox="0 0 100 50">
    <path d="M6 40 Q50 10 92 28 M82 20 L92 28 L80 34" stroke="#fff" stroke-width="2.5" fill="none"/>
  </svg>
  <svg class="arrow" style="left:733px" width="100" height="50" viewBox="0 0 100 50">
    <path d="M6 40 Q50 10 92 28 M82 20 L92 28 L80 34" stroke="#fff" stroke-width="2.5" fill="none"/>
  </svg>
</div>
</body>
</html>
```